brqnal new business card design project

we need a new business card design. you can view info about us @ brqnal-example.com. i have attached an example of our previous card with our previous name that we no longer use. We really liked the design, colors etc. look below to see more info about this project. it asks for a limited number of words. please see our website for more info about our compnay.

Target Market(s)

law enforcement

Contact Information for Business Card

i have uploaded an example of what we used before that we liked.

Font styles to use
Serif

```html
<!DOCTYPE html>
<html lang="en">
<head>
<meta charset="utf-8">
<title>brqnal business card</title>
<link rel="stylesheet" href="https://fonts.googleapis.com/css2?family=Caladea:wght@400;700&display=swap">
<style>
  :root {
    --navy: #0d2552;
    --navy-deep: #061640;
    --navy-light: #153566;
    --paper: #ffffff;
    --silver: #b7c1d2;
    --backdrop-top: #9a9a9a;
    --backdrop-bottom: #5a5a5a;
    --serif: "Caladea", "Cambria", Georgia, serif;
  }
  html, body {
    margin: 0;
    width: 1200px;
    height: 1200px;
    overflow: hidden;
  }
  body {
    background: linear-gradient(180deg, var(--backdrop-top), var(--backdrop-bottom));
    font-family: var(--serif);
    position: relative;
  }
  .card {
    position: absolute;
    left: 150px;
    width: 900px;
    height: 514px;
    border-radius: 4px;
    overflow: hidden;
    box-shadow: 0 14px 30px rgba(0,0,0,0.35);
  }
  .card--back {
    top: 60px;
    background: radial-gradient(ellipse at 25% 20%, var(--navy-light), var(--navy-deep) 80%);
    display: flex;
    align-items: center;
    justify-content: center;
  }
  .card--front {
    top: 626px;
    background: var(--paper);
  }
  .wordmark {
    font-family: var(--serif);
    font-weight: 400;
    letter-spacing: 0.14em;
    margin: 0;
    line-height: 1;
  }
  .card--back .wordmark {
    color: var(--paper);
    font-size: 120px;
  }
  .card--front .wordmark {
    position: absolute;
    left: 44px;
    top: 50px;
    color: var(--navy);
    font-size: 92px;
  }
  .swoosh {
    position: absolute;
    inset: 0;
    width: 900px;
    height: 514px;
  }
  .contact {
    position: absolute;
    left: 44px;
    right: 150px;
    bottom: 26px;
    color: var(--paper);
  }
  .contact__person {
    text-align: right;
    margin-bottom: 4px;
  }
  .contact__name {
    font-size: 30px;
    font-weight: 700;
    letter-spacing: 0.02em;
    margin: 0;
  }
  .contact__role {
    font-size: 17px;
    margin: 0 0 2px;
  }
  .contact__tel {
    font-size: 22px;
    margin: 0;
  }
  .contact__online {
    font-size: 20px;
    margin: 0 0 8px;
  }
  .contact__rule {
    border: 0;
    border-top: 1.5px solid rgba(255,255,255,0.75);
    margin: 0 0 8px;
  }
  .contact__address {
    font-size: 23px;
    margin: 0;
  }
</style>
</head>
<body>
  <section class="card card--back">
    <p class="wordmark">BRQNAL</p>
  </section>

  <section class="card card--front">
    <svg class="swoosh" viewBox="0 0 900 514" aria-hidden="true">
      <defs>
        <linearGradient id="navyFill" x1="0" y1="0" x2="0" y2="1">
          <stop offset="0" stop-color="#102b5c"/>
          <stop offset="1" stop-color="#061640"/>
        </linearGradient>
      </defs>
      <path d="M0,118 C150,150 360,270 600,318 C390,292 170,212 0,184 Z" fill="var(--silver)"/>
      <path d="M0,190 C190,215 420,335 640,335 C770,335 850,395 900,450 L900,514 L0,514 Z" fill="url(#navyFill)"/>
    </svg>
    <p class="wordmark">BRQNAL</p>
    <div class="contact">
      <div class="contact__person">
        <p class="contact__name">DANA WHITFIELD</p>
        <p class="contact__role">Creative Designer</p>
        <p class="contact__tel">Tel: 555.014.2290</p>
      </div>
      <p class="contact__online">Email: info@brqnal-example.com | Web: www.brqnal-example.com</p>
      <hr class="contact__rule">
      <p class="contact__address">1420 Alder Crest Lane, Fairbrook, TX 75000</p>
    </div>
  </section>
</body>
</html>
```